BRISKEL Need a luxury modern business card designed.

Need a luxury modern business card designed. refer to the uploaded files for the company name and logo in the zip file under source files. i will making my descion on monday. so please send in before then so if we need to edit we will have the time. we have a trade show coming up and im on a deadline for printer.

Target Market(s)

high end clients

Contact Information for Business Card

Company nAme and logo. Tobias Fennick Co-Founder / Project Manager Office # 555-318-7094 Cell # 555-642-1586 BRISKEL.CA Tobias@briskel-example.ca

Font styles to use
Other font styles liked:
• Modern

Requirements
Must have
• Company name and logo, contact info, using the black, gold and white color scheme.

```html
<!DOCTYPE html>
<html lang="en">
<head>
<meta charset="UTF-8">
<title>BRISKEL — Business Card</title>
<link rel="stylesheet" href="https://fonts.googleapis.com/css2?family=Arimo:wght@400;700&display=swap">
<style>
  :root {
    --backdrop: #2b2b2b;
    --card-black: #0c0c0c;
    --card-black-soft: #161616;
    --gold: #b4a268;
    --white: #f4f4f2;
    --rule: #8a8a8a;
  }
  * { margin: 0; padding: 0; box-sizing: border-box; }
  html, body {
    width: 1200px;
    height: 900px;
    overflow: hidden;
  }
  body {
    background: var(--backdrop);
    position: relative;
    font-family: "Arimo", Arial, sans-serif;
  }
  .card {
    position: absolute;
    left: 320px;
    width: 560px;
    height: 320px;
    background: linear-gradient(160deg, var(--card-black-soft), var(--card-black) 70%);
    border-bottom: 9px solid var(--gold);
    color: var(--white);
    display: flex;
    flex-direction: column;
    align-items: center;
  }
  .card--front { top: 100px; justify-content: center; }
  .card--back { top: 470px; padding-top: 44px; }

  .brand {
    display: flex;
    align-items: center;
    gap: 16px;
  }
  .brand__mark {
    width: 22px;
    height: 22px;
    background: var(--gold);
  }
  .brand__name {
    font-family: "Arimo", Arial, sans-serif;
    font-weight: 400;
    font-size: 44px;
    letter-spacing: 8px;
    line-height: 1;
    color: var(--white);
  }
  .card--back .brand__mark { width: 18px; height: 18px; }
  .card--back .brand__name { font-size: 38px; letter-spacing: 7px; }

  .contact {
    margin-top: 30px;
    text-align: center;
    font-size: 16px;
    line-height: 1.4;
  }
  .contact__name {
    font-weight: 700;
    font-size: 17px;
    letter-spacing: 0.5px;
    color: var(--gold);
  }
  .contact__title { margin-bottom: 6px; }
  .contact__divider {
    width: 120px;
    height: 1px;
    margin: 0 auto 6px;
    background: var(--rule);
  }
  .contact__label { color: var(--gold); font-weight: 700; }
</style>
</head>
<body>
  <section class="card card--front">
    <div class="brand">
      <span class="brand__mark" aria-hidden="true"></span>
      <span class="brand__name">BRISKEL</span>
    </div>
  </section>

  <section class="card card--back">
    <div class="brand">
      <span class="brand__mark" aria-hidden="true"></span>
      <span class="brand__name">BRISKEL</span>
    </div>
    <div class="contact">
      <p class="contact__name">TOBIAS FENNICK</p>
      <p class="contact__title">Co-Founder / Project Manager</p>
      <div class="contact__divider"></div>
      <p><span class="contact__label">P:</span> 555-318-7094 &nbsp;| <span class="contact__label">M:</span> 555-642-1586</p>
      <p>briskel.ca tobias@briskel-example.ca</p>
    </div>
  </section>
</body>
</html>
```